Thornbury Building Company - Card Design

I am looking to use the logo designs that you already did for me to develop a business card. I would like the card to have a black background and be double sided. I want white and green logo and text. I have attached an inspiration photo of a look that I like. I would like to use the Vertical Logo attached to take up the full front side of the card. On the back where I have my name and information, I would like to have the horizontal logo or maybe even just the image of the 'A' and trees without the text. I am open, but I am looking for something clean and simple and I want the green to really pop! Additional files can be found under Design #: 58302946

Target Market(s)

Homeowners

Industry/Entity Type

Construction

Contact Information for Business Card

Name: Marcus Thornbury, Title: Project Manager, Phone: 555.274.8136, Email: thornburybuildingcompany@mailvesta.com, address: 487 Larkspur Ln, Felton, CA 95033, Lic# 2468317

Colors
00AB8E
00BBA5
67D7C9
C6EFE9
E9F9F6

Requirements
Nice to have
• I would like to see the logos that I have already got from ArtLoomHub, though I am open to new ones

```html
<!DOCTYPE html>
<html lang="en">
<head>
<meta charset="UTF-8">
<title>Thornbury Building Company – Business Card</title>
<link href="https://fonts.googleapis.com/css2?family=Montserrat:wght@400;500;600;700&display=swap" rel="stylesheet">
<style>
  :root {
    --backdrop: #d9d4cc;
    --card: #232323;
    --white: #ffffff;
    --green: #6cbd45;
    --text-soft: #e8e8e8;
  }
  * { margin: 0; padding: 0; box-sizing: border-box; }
  html, body { width: 900px; height: 1200px; overflow: hidden; }
  body {
    background: var(--backdrop);
    font-family: "Montserrat", Arial, sans-serif;
    position: relative;
  }
  .card {
    position: absolute;
    left: 80px;
    width: 742px;
    height: 440px;
    background: var(--card);
    border-radius: 32px;
    color: var(--white);
  }
  .card--back { top: 132px; }
  .card--front { top: 640px; }

  /* back side: brand + contact */
  .brand-small {
    position: absolute;
    left: 40px;
    width: 300px;
    top: 182px;
    text-align: center;
  }
  .brand-mark {
    display: inline-block;
    background: var(--green);
  }
  .brand-small .brand-mark { width: 22px; height: 22px; margin-bottom: 12px; }
  .brand-name {
    font-weight: 700;
    color: var(--white);
    letter-spacing: 0.5px;
    line-height: 1.15;
  }
  .brand-small .brand-name { font-size: 24px; }

  .divider {
    position: absolute;
    left: 335px;
    top: 150px;
    width: 2px;
    height: 192px;
    background: var(--green);
  }
  .contact {
    position: absolute;
    left: 372px;
    top: 144px;
  }
  .contact__name {
    color: var(--green);
    font-weight: 600;
    font-size: 26px;
    line-height: 1.2;
  }
  .contact__title { font-size: 16px; color: var(--text-soft); margin-top: 2px; }
  .contact__licence { font-size: 16px; margin-top: 18px; font-weight: 600; }
  .contact__licence span { color: var(--green); font-weight: 500; }
  .contact__list { list-style: none; margin-top: 18px; }
  .contact__list li {
    display: flex;
    align-items: center;
    gap: 10px;
    font-size: 14px;
    color: var(--text-soft);
    line-height: 23px;
  }
  .contact__list svg { width: 14px; height: 14px; flex: none; }
  .contact__address {
    font-size: 16px;
    color: var(--text-soft);
    margin-top: 14px;
    line-height: 20px;
  }

  /* front side: large brand */
  .brand-large {
    position: absolute;
    inset: 0;
    display: flex;
    flex-direction: column;
    align-items: center;
    justify-content: center;
    text-align: center;
  }
  .brand-large .brand-mark { width: 40px; height: 40px; margin-bottom: 26px; }
  .brand-large .brand-name { font-size: 46px; letter-spacing: 1px; }
</style>
</head>
<body>

  <section class="card card--back" aria-label="Business card, contact side">
    <div class="brand-small">
      <span class="brand-mark" aria-hidden="true"></span>
      <p class="brand-name">Thornbury<br>Building Company</p>
    </div>

    <div class="divider"></div>

    <div class="contact">
      <h1 class="contact__name">Marcus Thornbury</h1>
      <p class="contact__title">Project Manager</p>
      <p class="contact__licence"><span>Lic</span> #2468317</p>
      <ul class="contact__list">
        <li>
          <svg viewBox="0 0 16 16" aria-hidden="true"><path fill="#6cbd45" d="M2 6c0-2 2.5-3 6-3s6 1 6 3v1h-3V5.5C10 5 9 5 8 5s-2 0-3 .5V7H2z M4 8h8l1.5 5h-11z"/></svg>
          555.274.8136
        </li>
        <li>
          <svg viewBox="0 0 16 16" aria-hidden="true"><path fill="#6cbd45" d="M1 3h14v10H1z"/><path fill="none" stroke="#232323" stroke-width="1.4" d="M1.5 3.5 8 9l6.5-5.5"/></svg>
          thornburybuildingcompany@mailvesta.com
        </li>
      </ul>
      <p class="contact__address">487 Larkspur Ln, Felton<br>CA 95033</p>
    </div>
  </section>

  <section class="card card--front" aria-label="Business card, brand side">
    <div class="brand-large">
      <span class="brand-mark" aria-hidden="true"></span>
      <p class="brand-name">Thornbury<br>Building Company</p>
    </div>
  </section>

</body>
</html>
```